Building company buisness cards

We are looking for a sharp modern new look for our business cards.
We are a New Zealand based company that specialises in house and land packages.
We have attached a photo of the current logo and would like to see if it can be improved somehow if needed.
We are open to any colours but we have chosen green at this stage.
Feel free to change the font and make the logo smarter looking.
Play with the colours and see what looks best.

We want a card that looks so good know one will want to throw it away!

Target Market(s)

Home buyers

Industry/Entity Type

Building

Contact Information for Business Card

Derek Tolvane
0217394062
dtolvane@quillmarkhomesteads.co.nz
quillmarkhomesteads.co.nz

Font styles to use
Serif
Sans Serif

Colors

Designer to choose colors to be used in the design.

Requirements
Must have
• Logo and company name on one side, details on the other side
Nice to have
• Color codes for the original green are HEX #4a8028, RGB(74,128,40), CMYK(42,0,69,50)
• Round corners, Raised and/or spot UV

```html
<!DOCTYPE html>
<html lang="en">
<head>
<meta charset="utf-8">
<title>Quillmark Homesteads – Business Cards</title>
<link href="https://fonts.googleapis.com/css2?family=Cinzel:wght@400&family=Jost:wght@400&display=swap" rel="stylesheet">
<style>
  :root {
    --backdrop: #3a302b;
    --card: #1b1d1f;
    --card-edge: #25282a;
    --silver: #cfd0d1;
    --brand-green: #4a8028;
    --text-light: #f2f2f2;
  }
  html, body {
    margin: 0;
    padding: 0;
    width: 1200px;
    height: 864px;
    overflow: hidden;
    background: var(--backdrop);
  }
  .canvas {
    position: relative;
    width: 1200px;
    height: 864px;
    display: flex;
    align-items: center;
    justify-content: center;
    gap: 48px;
  }
  .card {
    position: relative;
    width: 528px;
    height: 302px;
    background: var(--card);
    border-radius: 10px;
    box-shadow: 0 0 0 1px var(--card-edge), 0 14px 30px rgba(0,0,0,0.45);
    box-sizing: border-box;
  }
  /* Front: company name */
  .card-front {
    display: flex;
    flex-direction: column;
    align-items: center;
    justify-content: center;
  }
  .brand-mark {
    width: 26px;
    height: 26px;
    background: var(--silver);
    margin-bottom: 18px;
  }
  .brand-name {
    font-family: "Cinzel", "Times New Roman", serif;
    font-weight: 400;
    color: var(--silver);
    text-align: center;
    line-height: 1.05;
    margin: 0;
  }
  .brand-name .line-one { display: block; font-size: 38px; letter-spacing: 1px; }
  .brand-name .line-two { display: block; font-size: 28px; letter-spacing: 1px; }
  /* Back: contact details */
  .card-back {
    display: flex;
    align-items: center;
    justify-content: flex-end;
    padding-right: 44px;
  }
  .contact {
    text-align: center;
  }
  .contact-name {
    font-family: "Cinzel", "Times New Roman", serif;
    font-weight: 400;
    font-size: 23px;
    letter-spacing: 1px;
    color: var(--brand-green);
    margin: 0 0 8px;
  }
  .contact-line {
    font-family: "Jost", "Futura", sans-serif;
    font-size: 15px;
    line-height: 1.3;
    color: var(--text-light);
    margin: 0;
  }
</style>
</head>
<body>
  <main class="canvas">
    <section class="card card-front" aria-label="Card front">
      <div class="brand-mark"></div>
      <h1 class="brand-name">
        <span class="line-one">Quillmark</span>
        <span class="line-two">Homesteads.</span>
      </h1>
    </section>
    <section class="card card-back" aria-label="Card back">
      <div class="contact">
        <h2 class="contact-name">DEREK TOLVANE</h2>
        <p class="contact-line">Ph. 0217394062</p>
        <p class="contact-line">dtolvane@quillmarkhomesteads.co.nz</p>
        <p class="contact-line">quillmarkhomesteads.co.nz</p>
      </div>
    </section>
  </main>
</body>
</html>
```